I would like a business card to match my truck wrap and logo. I would like the font to match my existing business card please.

Industry/Entity Type

Painter

Contact Information for Business Card

Rodrigo Fenwar 801-437-2190 Fenwarcoatings.utah@brelmox.com
SERVICES - Custom Paint & Stain, Interior & Exterior, Epoxy Coatings / Garage Floors, Cabinet Refinishing, Log Staining and Refinishing.

Requirements
Nice to have
• I would like to have the white and grey line like the bottom of my vehicle wrap, Light Grey to match my truck also.

```html
<!DOCTYPE html>
<html lang="en">
<head>
<meta charset="utf-8">
<title>Fenwar Coatings – Business Card</title>
<link href="https://fonts.googleapis.com/css2?family=Russo+One&family=Arimo:wght@400;700&display=swap" rel="stylesheet">
<style>
  :root {
    --blue-bright: #0aa9e8;
    --blue-mid: #0a86cf;
    --blue-deep: #0b5fa3;
    --name-blue: #0b6db6;
    --rule-grey: #b4b7c4;
    --ink: #1f2430;
    --paper: #ffffff;
    --stage: #e9ebef;
  }
  * { margin: 0; padding: 0; box-sizing: border-box; }
  html, body { width: 1200px; height: 900px; overflow: hidden; background: var(--stage); }
  .canvas {
    width: 1200px; height: 900px;
    display: flex; flex-direction: column; align-items: center; justify-content: center; gap: 36px;
  }
  .card { width: 700px; height: 400px; position: relative; overflow: hidden; box-shadow: 0 6px 18px rgba(0,0,0,.18); }

  /* Services side */
  .card-services {
    background: linear-gradient(160deg, var(--blue-bright) 0%, var(--blue-mid) 50%, var(--blue-deep) 100%);
    display: flex; align-items: center; justify-content: center;
  }
  .services-mark {
    position: absolute; left: 190px; top: 70px; width: 260px; height: 260px;
    background: rgba(255,255,255,.07); border-radius: 14px; transform: rotate(45deg);
  }
  .services-list {
    position: relative; list-style: none; text-align: center;
    font-family: "Arimo", Arial, sans-serif; color: var(--paper);
    font-size: 19px; line-height: 1.75; letter-spacing: .3px; text-transform: uppercase;
  }

  /* Contact side */
  .card-contact { background: var(--paper); }
  .card-frame { position: absolute; inset: 0; }
  .brand {
    position: absolute; left: 70px; top: 170px; width: 250px;
    font-family: "Russo One", sans-serif; color: var(--blue-bright); text-align: center;
  }
  .brand-square { width: 34px; height: 34px; background: var(--blue-bright); margin: 0 auto 14px; }
  .brand-name { font-size: 44px; line-height: 1; }
  .brand-sub { font-size: 18px; letter-spacing: 11px; margin-top: 8px; padding-left: 11px; }
  .divider { position: absolute; left: 340px; top: 120px; width: 1px; height: 170px; background: linear-gradient(#fff, #c9ccd4, #fff); }
  .contact { position: absolute; left: 370px; top: 135px; font-family: "Arimo", Arial, sans-serif; color: var(--ink); }
  .contact-name { font-family: "Russo One", sans-serif; font-size: 30px; color: var(--name-blue); margin-bottom: 18px; }
  .contact-line { display: flex; align-items: center; gap: 10px; font-size: 16px; line-height: 1.6; }
  .contact-line svg { width: 17px; height: 17px; fill: var(--blue-mid); flex: none; }
</style>
</head>
<body>
<main class="canvas">
  <section class="card card-services" aria-label="Services side">
    <div class="services-mark" aria-hidden="true"></div>
    <ul class="services-list">
      <li>Custom Paint &amp; Stain</li>
      <li>Interior &amp; Exterior</li>
      <li>Epoxy Coatings / Garage Floors</li>
      <li>Cabinet Refinishing</li>
      <li>Log Staining and Refinishing.</li>
    </ul>
  </section>

  <section class="card card-contact" aria-label="Contact side">
    <svg class="card-frame" viewBox="0 0 700 400" aria-hidden="true">
      <defs>
        <linearGradient id="bandBlue" x1="0" y1="0" x2="0" y2="1">
          <stop offset="0" stop-color="#0aa9e8"/>
          <stop offset="1" stop-color="#0b74c2"/>
        </linearGradient>
      </defs>
      <rect width="700" height="400" fill="url(#bandBlue)"/>
      <polygon fill="#ffffff" points="0,95 130,95 170,45 700,45 700,300 560,300 520,360 0,360"/>
      <polyline fill="none" stroke="#b4b7c4" stroke-width="3" points="0,88 126,88 166,38 700,38"/>
      <polyline fill="none" stroke="#b4b7c4" stroke-width="3" points="0,367 524,367 564,307 700,307"/>
    </svg>

    <div class="brand">
      <div class="brand-square" aria-hidden="true"></div>
      <div class="brand-name">FENWAR</div>
      <div class="brand-sub">COATINGS</div>
    </div>

    <div class="divider" aria-hidden="true"></div>

    <div class="contact">
      <p class="contact-name">RODRIGO FENWAR</p>
      <p class="contact-line">
        <svg viewBox="0 0 24 24" aria-hidden="true"><path d="M6.6 10.8a15.1 15.1 0 0 0 6.6 6.6l2.2-2.2a1 1 0 0 1 1-.25 11.4 11.4 0 0 0 3.6.57 1 1 0 0 1 1 1V20a1 1 0 0 1-1 1A17 17 0 0 1 3 4a1 1 0 0 1 1-1h3.5a1 1 0 0 1 1 1c0 1.25.2 2.45.57 3.6a1 1 0 0 1-.25 1z"/></svg>
        801-437-2190
      </p>
      <p class="contact-line">
        <svg viewBox="0 0 24 24" aria-hidden="true"><path d="M2 5h20v14H2z M2 5l10 8 10-8" fill="currentColor" stroke="#fff" stroke-width="1.5" style="color:#0a86cf"/></svg>
        Fenwarcoatings.utah@brelmox.com
      </p>
    </div>
  </section>
</main>
</body>
</html>
```